Brightfen Business Card Redesign & Logo Update

We need to update our business cards to something more modern and fresh. Brightfen can provide the current color schemes and old design examples, but welcome creativity in helping us with this redesign. PLEASE NOTE that we no longer utilize the "tree" and/or "leaf" imagery in our branding. If able would apprecaite an update on the quality of our "words only" logo in Ai. / PNG formats too.

Target Market(s)

Investors, landowners, corporate partners, contractors

Industry/Entity Type

Environmental Restoration & Conservation

Contact Information for Business Card

Logo, persons name, title, mailing address, phone and email, website url

Font styles to use
Other font styles liked:
• Merriweather

Requirements
Nice to have
• Logo, persons name, title, mailing address, phone and email, website url, but open to ideams
Should not have
• No all back backgrounds

```html
<!DOCTYPE html>
<html lang="en">
<head>
<meta charset="utf-8">
<title>Brightfen Business Card</title>
<link href="https://fonts.googleapis.com/css2?family=Open+Sans:wght@400;700;800&display=swap" rel="stylesheet">
<style>
  :root {
    --backdrop: #2a2b2e;
    --card: #ffffff;
    --orange: #ec7b23;
    --green: #177a3c;
    --ink: #1b1b1b;
    --rule: #1b1b1b;
  }
  * { margin: 0; padding: 0; box-sizing: border-box; }
  html, body {
    width: 1200px; height: 780px; overflow: hidden;
    background: var(--backdrop);
    font-family: "Open Sans", sans-serif;
    color: var(--ink);
  }
  .canvas { position: relative; width: 1200px; height: 780px; }
  .card {
    position: absolute;
    width: 540px; height: 309px;
    background: var(--card);
    box-shadow: 0 6px 18px rgba(0,0,0,.45);
  }
  .card--front { left: 70px; top: 60px; }
  .card--back { left: 590px; top: 410px; }

  .wordmark {
    font-family: "Open Sans", sans-serif;
    font-weight: 800;
    color: var(--green);
    letter-spacing: -1px;
    line-height: 1;
  }
  .card--front .wordmark {
    position: absolute; left: 0; right: 0; top: 118px;
    text-align: center; font-size: 76px;
  }
  .card--back .wordmark {
    position: absolute; left: 34px; top: 40px; font-size: 44px;
  }

  .person { position: absolute; left: 44px; top: 178px; }
  .person__name { font-size: 26px; font-weight: 800; line-height: 1.1; }
  .person__first { color: var(--orange); }
  .person__last { color: var(--green); }
  .person__title { font-size: 15px; margin-top: 4px; }

  .divider {
    position: absolute; left: 44px; right: 30px; top: 244px;
    height: 1.5px; background: var(--rule);
  }

  .contacts {
    position: absolute; left: 44px; right: 30px; top: 258px;
    display: flex; justify-content: space-between; align-items: center;
    font-size: 12.5px;
  }
  .contact { display: flex; align-items: center; gap: 7px; }
  .contact__icon { width: 15px; height: 15px; flex: none; }
</style>
</head>
<body>
<main class="canvas">
  <section class="card card--front" aria-label="Card front">
    <div class="wordmark">Brightfen</div>
  </section>

  <section class="card card--back" aria-label="Card back">
    <div class="wordmark">Brightfen</div>

    <div class="person">
      <div class="person__name"><span class="person__first">Lena</span> <span class="person__last">Marsh</span></div>
      <div class="person__title">Managing Director</div>
    </div>

    <div class="divider"></div>

    <div class="contacts">
      <div class="contact">
        <svg class="contact__icon" viewBox="0 0 16 16" aria-hidden="true">
          <path fill="var(--orange)" d="M3.5 1.5l2.3 2.6-1.3 1.7c.9 2 2.7 3.8 4.7 4.7l1.7-1.3 2.6 2.3-1.5 2.2C6.5 13.4 2.6 9.5 1.3 3z"/>
        </svg>
        <span>+469-555-0142</span>
      </div>
      <div class="contact">
        <svg class="contact__icon" viewBox="0 0 16 16" aria-hidden="true">
          <rect x="1" y="3" width="14" height="10" rx="1" fill="var(--orange)"/>
          <path d="M1.5 3.8L8 9l6.5-5.2" fill="none" stroke="#fff" stroke-width="1.3"/>
        </svg>
        <span>info@brightfen-mail.com</span>
      </div>
      <div class="contact">
        <svg class="contact__icon" viewBox="0 0 16 16" aria-hidden="true">
          <circle cx="8" cy="8" r="7" fill="var(--orange)"/>
          <path d="M1 8h14M8 1c-2.5 2-2.5 12 0 14M8 1c2.5 2 2.5 12 0 14" fill="none" stroke="#fff" stroke-width="1"/>
        </svg>
        <span>www.brightfen-web.com</span>
      </div>
    </div>
  </section>
</main>
</body>
</html>
```